Automotive component supplier needs a business card design

We need a business card design for our company called Velran Global Components Ltd based in the UK. We are a supplier of interior and exterior components to premium car manufacturers such as Corvel Ashby, Hadley Fenn, Marquist and Tavarelli. We would like to see a modern business card design that uses the colour blue.

Target Market(s)

Premium automotive car manufacturers.

Industry/Entity Type

Automotive

Contact Information for Business Card

Company Name : Velran Global Components Limited
Address: 17 Marlow Yard, Upper Heath, Warwick, CV31 8QL, United Kingdom
Web Address : www.velrancomponents-example.co.uk

Font styles to use
Other font styles liked:
• Helvetica

Colors
3176b5
0255a3
85acd3
cfdeed
cee9f5
85cae6
34a6d7
0692cd
9bcb3c

Requirements
Must have
• Clear company logo and a mixture of blue colours.
Nice to have
• A high quality modern image.
Should not have
• Multiple colours.

```html
<!DOCTYPE html>
<html lang="en">
<head>
<meta charset="utf-8">
<title>Velran Global Components – Business Card</title>
<link href="https://fonts.googleapis.com/css2?family=Arimo:wght@400;700&display=swap" rel="stylesheet">
<style>
  :root {
    --stage: #2e2e2e;
    --card-white: #f6f6f6;
    --brand-blue: #0692cd;
    --deep-blue: #0a7fbf;
    --accent-green: #8bc53f;
    --text-grey: #5a5a5a;
    --rule-grey: #9a9a9a;
    --white: #ffffff;
  }
  * { margin: 0; padding: 0; box-sizing: border-box; }
  html, body { width: 1200px; height: 965px; overflow: hidden; }
  body {
    background: var(--stage);
    font-family: "Arimo", "Helvetica Neue", Helvetica, Arial, sans-serif;
    position: relative;
  }
  .card {
    position: absolute;
    left: 246px;
    width: 710px;
    height: 402px;
  }
  .card-front {
    top: 60px;
    background: radial-gradient(ellipse at 70% 20%, #ffffff 0%, var(--card-white) 55%, #e4e4e4 100%);
  }
  .card-back {
    top: 504px;
    background: var(--brand-blue);
  }

  /* front */
  .front-wordmark {
    position: absolute;
    left: 42px;
    top: 56px;
    color: var(--brand-blue);
    font-weight: 700;
  }
  .front-wordmark .mark-name {
    display: flex;
    align-items: center;
    gap: 14px;
    font-size: 84px;
    line-height: 1;
    letter-spacing: 2px;
  }
  .mark-square {
    width: 18px; height: 18px;
    background: var(--accent-green);
    align-self: flex-start;
    margin-top: 6px;
  }
  .front-wordmark .mark-sub {
    font-size: 20px;
    letter-spacing: 4.2px;
    margin-top: 8px;
  }
  .holder {
    position: absolute;
    right: 35px;
    top: 226px;
    text-align: right;
  }
  .holder-name {
    color: var(--deep-blue);
    font-size: 22px;
    font-weight: 700;
    letter-spacing: 0.3px;
  }
  .holder-role {
    color: var(--accent-green);
    font-size: 16px;
    margin-top: 6px;
  }
  .divider {
    position: absolute;
    top: 266px;
    left: 42px;
    width: 510px;
    height: 2px;
    display: flex;
  }
  .divider-solid { width: 383px; height: 2px; background: var(--rule-grey); }
  .divider-dotted {
    width: 120px; margin-left: 4px; height: 2px;
    background-image: radial-gradient(circle, var(--brand-blue) 1px, transparent 1.2px);
    background-size: 4px 2px;
  }
  .address {
    position: absolute;
    left: 42px;
    top: 311px;
    color: var(--text-grey);
    font-size: 15.5px;
    line-height: 20px;
  }
  .contacts {
    position: absolute;
    right: 35px;
    top: 297px;
    list-style: none;
    color: var(--text-grey);
    font-size: 15.5px;
    line-height: 20px;
  }
  .contacts li {
    display: flex;
    justify-content: flex-end;
    align-items: center;
    gap: 7px;
  }
  .contacts svg { width: 16px; height: 16px; fill: var(--brand-blue); }

  /* back */
  .back-wordmark {
    position: absolute;
    left: 0; right: 0;
    top: 120px;
    text-align: center;
    color: var(--white);
    font-weight: 700;
  }
  .back-wordmark .mark-name {
    font-size: 104px;
    line-height: 1;
    letter-spacing: 3px;
  }
  .back-wordmark .mark-sub {
    font-size: 27px;
    letter-spacing: 5.4px;
    margin-top: 10px;
  }
  .back-web {
    position: absolute;
    left: 0; right: 0;
    top: 370px;
    display: flex;
    justify-content: center;
    align-items: center;
    gap: 16px;
    color: var(--white);
    font-size: 15.5px;
  }
  .back-web .rule { width: 110px; height: 1.5px; background: rgba(255,255,255,0.8); }
</style>
</head>
<body>

<section class="card card-front" aria-label="Business card front">
  <div class="front-wordmark">
    <div class="mark-name"><span>VELRAN</span><span class="mark-square"></span></div>
    <div class="mark-sub">GLOBAL COMPONENTS</div>
  </div>

  <div class="holder">
    <div class="holder-name">DANIEL REEVE</div>
    <div class="holder-role">Founder &amp; CEO</div>
  </div>

  <div class="divider"><span class="divider-solid"></span><span class="divider-dotted"></span></div>

  <address class="address" style="font-style:normal">
    17 Marlow Yard, Upper Heath,<br>
    Warwick, CV31 8QL<br>
    United Kingdom
  </address>

  <ul class="contacts">
    <li>+ 041 555 30 47
      <svg viewBox="0 0 16 16" aria-hidden="true"><rect x="1" y="2" width="3" height="12" rx="1"/><rect x="5" y="3" width="10" height="11" rx="1"/><rect x="7" y="5" width="6" height="2" fill="#fff"/><rect x="7" y="9" width="2" height="2" fill="#fff"/><rect x="11" y="9" width="2" height="2" fill="#fff"/></svg>
    </li>
    <li>+ 0164 555 82 19
      <svg viewBox="0 0 16 16" aria-hidden="true"><rect x="4" y="1" width="8" height="14" rx="1.5"/><rect x="5.5" y="3" width="5" height="8" fill="#fff"/><circle cx="8" cy="13" r="0.9" fill="#fff"/></svg>
    </li>
    <li>info@velrancomponents-example.co.uk
      <svg viewBox="0 0 16 16" aria-hidden="true"><rect x="1" y="3" width="14" height="10" rx="1"/><path d="M1.5 3.8 8 9l6.5-5.2" stroke="#fff" stroke-width="1.3" fill="none"/></svg>
    </li>
    <li>www.velrancomponents-example.co.uk
      <svg viewBox="0 0 16 16" aria-hidden="true"><circle cx="8" cy="8" r="7"/><g stroke="#fff" stroke-width="1" fill="none"><ellipse cx="8" cy="8" rx="3" ry="6.3"/><line x1="1.5" y1="8" x2="14.5" y2="8"/><line x1="8" y1="1.5" x2="8" y2="14.5"/><path d="M2.6 4.8h10.8M2.6 11.2h10.8"/></g></svg>
    </li>
  </ul>
</section>

<section class="card card-back" aria-label="Business card back">
  <div class="back-wordmark">
    <div class="mark-name">VELRAN</div>
    <div class="mark-sub">GLOBAL COMPONENTS</div>
  </div>
  <div class="back-web">
    <span class="rule"></span>
    <span>www.velrancomponents-example.co.uk</span>
    <span class="rule"></span>
  </div>
</section>

</body>
</html>
```